New Business Card Options

we need a new business card design to reflect the edgy, innovative image we want the company to portray. We also need to include the social buttons to encourage more interaction with our social media accounts.
I've attached the current business card design which is a fold out card which has lines for writing notes on the back. I'm looking for options for design as well as printing suggestions - we want to stand out and be memorable.
THE BUSINESS CARD DOES NOT HAVE TO HAVE THE PHOTO
Colours to use:
MARINE
Dark blue R000 G031 B051
Light blue R080 G177 B234
Dark blue C100 M047 Y023 K079
Light blue C083 M001 Y000 K000
Updates
Reason: I just need an extra day to shortlist designs
Reason: need more time to decide
Target Market(s)
Marine
Industry/Entity Type
Business
Contact Information for Business Card
I've attached a copy of our current business card. the new business cards may or may not include the photo - i would like options of both. I would like our social media icons adding for Chirply, Workloop, Pagebrook and ReelDeck
Font styles to use
Other font styles liked:
- Calibri
Look and feel
Each slider illustrates characteristics of the customer's brand and the style your logo design should communicate.

```html
<!DOCTYPE html>
<html lang="en">
<head>
<meta charset="utf-8">
<title>Keeltide Marine – Business Card</title>
<link rel="stylesheet" href="https://fonts.googleapis.com/css2?family=Open+Sans:wght@300;400;600;700&display=swap">
<style>
  :root {
    --page-bg: #e3e5e7;
    --card-white: #ffffff;
    --card-blue: #0a8fd8;
    --navy: #001f33;
    --light-blue: #50b1ea;
    --text-grey: #4a4f55;
    --icon-grey: #8d9297;
    --icon-blue: #1f8fd6;
    --icon-green: #5cb346;
    --icon-orange: #f2a11f;
    --ring-pink: #e8305a;
    --ring-dark: #222628;
    --ring-orange: #f39a1e;
    --photo-tone-a: #d9d9d9;
    --photo-tone-b: #8a8a8a;
  }
  * { box-sizing: border-box; margin: 0; padding: 0; }
  html, body { width: 1118px; height: 1200px; overflow: hidden; }
  body {
    background: var(--page-bg);
    font-family: "Open Sans", Calibri, sans-serif;
    position: relative;
  }
  .card {
    position: absolute;
    left: 139px;
    width: 840px;
    height: 480px;
    border-radius: 34px;
    overflow: hidden;
    box-shadow: 0 6px 22px rgba(0,0,0,0.12);
  }
  /* Back side */
  .card-back { top: 70px; background: var(--card-white); }
  .brand {
    position: absolute;
    left: 70px;
    top: 190px;
    width: 320px;
    text-align: center;
  }
  .brand-name {
    font-weight: 700;
    font-size: 44px;
    color: var(--navy);
    letter-spacing: -0.5px;
    line-height: 1;
  }
  .brand-tagline {
    margin-top: 10px;
    font-weight: 700;
    font-size: 19px;
    color: var(--light-blue);
  }
  .divider-fold {
    position: absolute;
    left: 0; top: 0;
    width: 840px; height: 480px;
  }
  .contact-list {
    position: absolute;
    left: 444px;
    top: 96px;
    list-style: none;
  }
  .contact-item {
    display: flex;
    align-items: center;
    height: 70px;
  }
  .contact-icon {
    width: 70px; height: 70px;
    display: flex; align-items: center; justify-content: center;
  }
  .contact-icon.phone { background: var(--icon-grey); }
  .contact-icon.chat { background: var(--icon-blue); }
  .contact-icon.mail { background: var(--icon-green); }
  .contact-icon.web { background: var(--icon-orange); }
  .contact-text {
    margin-left: 26px;
    font-size: 21px;
    color: var(--text-grey);
  }
  /* Front side */
  .card-front { top: 640px; background: var(--card-blue); color: #fff; }
  .profile-link {
    position: absolute;
    right: 40px; top: 30px;
    display: flex; align-items: center; gap: 10px;
    font-size: 15px; line-height: 1.15;
  }
  .profile-link-mark {
    width: 26px; height: 26px; background: #fff; border-radius: 3px;
  }
  .portrait {
    position: absolute;
    left: 300px; top: 42px;
    width: 240px; height: 240px;
  }
  .identity {
    position: absolute;
    left: 0; top: 308px; width: 840px;
    display: flex; justify-content: center; align-items: center;
  }
  .person-name { font-weight: 700; font-size: 31px; }
  .identity-rule {
    width: 2px; height: 40px; background: rgba(255,255,255,0.55);
    margin: 0 22px;
  }
  .person-role { font-weight: 300; font-size: 27px; }
  .services {
    position: absolute;
    left: 0; top: 398px; width: 840px;
    display: flex; justify-content: center; gap: 34px;
    list-style: none;
    font-size: 24px;
  }
  .services li::before { content: "•"; margin-right: 8px; }
</style>
</head>
<body>

<section class="card card-back" aria-label="Card back">
  <svg class="divider-fold" viewBox="0 0 840 480" aria-hidden="true">
    <defs>
      <linearGradient id="foldShade" x1="0" x2="1">
        <stop offset="0" stop-color="#000" stop-opacity="0"/>
        <stop offset="1" stop-color="#000" stop-opacity="0.10"/>
      </linearGradient>
    </defs>
    <polygon points="390,0 430,0 430,480 390,480" fill="url(#foldShade)"/>
    <line x1="430" y1="0" x2="430" y2="480" stroke="#d6d8da" stroke-width="2"/>
  </svg>

  <div class="brand">
    <div class="brand-name">Keeltide Marine</div>
    <div class="brand-tagline">Innovative Ship Solutions</div>
  </div>

  <ul class="contact-list">
    <li class="contact-item">
      <span class="contact-icon phone">
        <svg width="34" height="34" viewBox="0 0 24 24" fill="none" stroke="#fff" stroke-width="1.8"><rect x="6" y="2" width="12" height="20" rx="2"/><line x1="10" y1="18" x2="14" y2="18"/></svg>
      </span>
      <span class="contact-text">+44 (0) 7700 900123</span>
    </li>
    <li class="contact-item">
      <span class="contact-icon chat">
        <svg width="34" height="34" viewBox="0 0 24 24" fill="none" stroke="#fff" stroke-width="1.8"><path d="M4 5h16v11H9l-5 4z"/></svg>
      </span>
      <span class="contact-text">sam.porter12</span>
    </li>
    <li class="contact-item">
      <span class="contact-icon mail">
        <svg width="34" height="34" viewBox="0 0 24 24" fill="none" stroke="#fff" stroke-width="1.8"><rect x="3" y="6" width="18" height="13"/><path d="M3 6l9 7 9-7"/></svg>
      </span>
      <span class="contact-text">sam.porter@keeltide-marine.com</span>
    </li>
    <li class="contact-item">
      <span class="contact-icon web">
        <svg width="34" height="34" viewBox="0 0 24 24" fill="none" stroke="#fff" stroke-width="1.6"><circle cx="12" cy="12" r="9"/><ellipse cx="12" cy="12" rx="4" ry="9"/><line x1="3" y1="12" x2="21" y2="12"/></svg>
      </span>
      <span class="contact-text">www.keeltide-marine.com</span>
    </li>
  </ul>
</section>

<section class="card card-front" aria-label="Card front">
  <div class="profile-link">
    <span class="profile-link-mark"></span>
    <span>Find me on<br>Workloop</span>
  </div>

  <svg class="portrait" viewBox="0 0 240 240">
    <defs>
      <radialGradient id="photoTone" cx="0.5" cy="0.4" r="0.6">
        <stop offset="0" stop-color="var(--photo-tone-a)"/>
        <stop offset="1" stop-color="var(--photo-tone-b)"/>
      </radialGradient>
    </defs>
    <circle cx="120" cy="120" r="114" fill="#0a7fc2"/>
    <g fill="none" stroke-width="9" transform="rotate(-200 120 120)">
      <circle cx="120" cy="120" r="113" stroke="var(--ring-pink)" stroke-dasharray="190 520"/>
      <circle cx="120" cy="120" r="113" stroke="var(--ring-dark)" stroke-dasharray="0 190 250 300"/>
      <circle cx="120" cy="120" r="113" stroke="var(--ring-orange)" stroke-dasharray="0 520 180 10"/>
    </g>
    <circle cx="120" cy="120" r="104" fill="#fff"/>
    <circle cx="120" cy="120" r="96" fill="url(#photoTone)" role="img" aria-label="Portrait photo of the card holder"/>
  </svg>

  <div class="identity">
    <span class="person-name">Sam Porter</span>
    <span class="identity-rule"></span>
    <span class="person-role">Regional Manager</span>
  </div>

  <ul class="services">
    <li>Environmental</li>
    <li>Medical</li>
    <li>Navigation</li>
    <li>Safety</li>
  </ul>
</section>

</body>
</html>
```